Systems and Technology Consultants - Website

Design & Build a website for a new company which operates in the Systems and Technology space for Transportation, Government and Commercial sectors.

Overall design should be minimalist in nature.
Should also have a feed that provides news and event updates on the main page.
Logo has already been awarded and should be incorporated into the site.

We like the overall layout, functionality and simplicity of the below sites. Submitted designs could be similar to or a combination of the aspects on these sites, or perhaps a whole different concept - we are open to new ideas.
Norvique.com
Teblo.it

Update 1 Dated 27 May 2014

All I am moving away from the Teblo.it website and would like it to be more aligned with Norvique.com not only in layout but in functionality. I will be extending the deadline of this design brief for two weeks to incorporate additional requirements and will add addtional funding to the project.

Apologies for not having more information available to provide but with so many submissions its getting confusing.

Thanks Derek

Please note that the brief has been updated and the deadline has been extended.

Important: We will need two language versions of the website, English and Arabic; the website is hosted on HostPelican

Hello All, Thank you for your submissions. We have narrowed it down to the final 6 designers and I just wanted to take a moment and provide a bit of feedback regarding the concepts that we like and the modifications we are looking for. First, let me mention some of the design functions we like. - At the top of the homepage we really like the "region" or "language" tab so that the website can be viewed in both English and Arabic. - We like the homepage to have clear color variation so that the different sections of the homepage are distinct. Additionally, we like the bottom portion of the homepage to be in red. We feel that draws attention to our contact information. Again, we would like the colors to integrate black, gray-scale, red, etc. - Having a search tab at the top of the home page, or integrated into the main image, so that the site is easy to navigate. - We especially like the main image to have the scrolling tabs at the bottom so it is easy to browse the services offered (Consultancy, Solutions Architecture, Masters Systems Integration, Independent Design Review). - In regards to the services offered tab we really like the idea that a few people presented that have the outside of our logo with an icon in the middle of consultancy, solutions, etc., etc. Secondly, as mentioned in our brief we really enjoy the design of norvique site. Specially, we enjoy the strong iconic images they use, the way the tabs at the top scroll easily, and contact us page that generates an email. Lastly, I've included some photos of the concept we have been working on. What we are trying to demonstrate is how our company offers a range of services that are essentially linked together. We provide individual services that when combined present the full service package. We would like this concept to be integrated into the over concept of our website. Please feel free to ask for clarification of any of the above points or contact us if you have any additional questions. We appreciate all of your hard work and are very excited to see the updated designs. Best, Marta Vennick Quelbrant Senior Program Manager marta.vennick@quelbrant-example.com

Industry/Entity Type

Government

Font styles to use
Serif
Sans Serif

Requirements
Must have
• Must work on/adapt to various/mobile devices (responsive)
Must be simple and straightforward
Colors should be in line/matching with logo
2 language versions: English and Arabic (no Thai)
Services should be the first group/row of items after/below the main image
Note: the website will be hosted by hostpelican
Nice to have
• Submit feedback form
What's New section
The banner at the bottom of the site should not be too large; we would like a narrow one more
It would be nice if the header/top banner (with Home, About, etc. tabs) could stay in place as you scroll down (like Norvique and Chatterloop)
We will likely only use one image with a Company slogan on the Home page rather than a carousel of images to rotate through
Should not have
• This is the existing website: http://www.quelbrant-example.org
We do not like the animation, the way the banner icons/titles bounce
Not simple enough, we don't like the functionality or how pages load so slowly
We do not like the logo centered - it should be at the left
The banner and its tabs should not be towards the right, we would like them to be centered, to go all the way across and to be below the logo

```html
<!DOCTYPE html>
<html lang="en">
<head>
<meta charset="utf-8">
<title>Quelbrant – Systems and Technology Consultants</title>
<link href="https://fonts.googleapis.com/css2?family=Open+Sans:ital,wght@0,400;0,600;0,700;1,400;1,600;1,700&display=swap" rel="stylesheet">
<style>
:root{
  --red:#e3232b;
  --ink:#222;
  --body:#444;
  --muted:#888;
  --line:#e6e6e6;
  --panel:#f7f7f7;
  --footer:#3a3a3a;
  --white:#fff;
}
*{box-sizing:border-box;margin:0;padding:0}
html,body{width:876px;height:1200px;overflow:hidden;background:var(--white);font-family:"Open Sans",sans-serif;color:var(--ink)}
.page{position:relative;width:876px;height:1200px}
.abs{position:absolute}

/* header */
.site-header{position:absolute;left:0;top:0;width:876px;height:91px;border-bottom:1px solid var(--line);background:var(--white)}
.brand{left:124px;top:8px;width:86px;text-align:center}
.brand-mark{display:block;width:44px;height:44px;margin:0 auto 6px;border-radius:50%;background:var(--red)}
.brand-name{font-size:10px;font-weight:700;letter-spacing:2px;color:var(--red)}
.partner{left:480px;top:22px;font-size:8px;font-weight:700;display:flex;align-items:center;gap:6px}
.partner-dot{width:11px;height:11px;border-radius:50%;background:#2f8fd8}
.search-field{left:545px;top:16px;width:99px;height:24px;border:1px solid #d6d6d6;border-radius:2px;font-size:8px;color:var(--muted);padding:6px 9px}
.search-select{left:652px;top:16px;width:61px;height:24px;border:1px solid #d6d6d6;border-radius:2px;font-size:8px;color:var(--muted);padding:6px 9px}
.search-select::after{content:"";position:absolute;right:8px;top:10px;border:4px solid transparent;border-top-color:#555}
.search-btn{left:721px;top:16px;width:31px;height:24px;background:var(--red);border-radius:2px}
.main-nav{left:337px;top:58px;font-size:11.5px;color:var(--ink)}
.main-nav span{position:absolute;white-space:nowrap}

/* hero */
.hero{left:0;top:91px;width:876px;height:357px;
  background:
    radial-gradient(ellipse 160px 200px at 420px 120px,rgba(255,255,255,.85),rgba(255,255,255,0) 70%),
    radial-gradient(ellipse 260px 140px at 700px 170px,rgba(40,44,50,.75),rgba(40,44,50,0) 75%),
    linear-gradient(100deg,#4a4a4c 0%,#6e6e70 18%,#bdbdbd 34%,#eeeeee 46%,#c8c8c8 58%,#7c7f84 74%,#3f4247 100%)}
.hero-title{left:128px;top:217px;width:421px;height:49px;background:rgba(40,40,40,.72);color:var(--white);font-style:italic;font-weight:700;font-size:20.5px;line-height:49px;padding-left:10px;letter-spacing:-.4px;white-space:nowrap}
.hero-sub{left:128px;top:272px;width:287px;height:29px;background:rgba(60,60,60,.6);color:var(--white);font-style:italic;font-weight:400;font-size:18px;line-height:28px;padding-left:10px;white-space:nowrap}
.hero-arrow{width:26px;height:26px;border-radius:50%;background:rgba(255,255,255,.9);box-shadow:0 0 0 4px rgba(0,0,0,.25)}

/* services */
.service{top:470px;width:200px;text-align:center}
.service svg{display:block;margin:0 auto}
.service h3{font-weight:400;font-size:12px;margin-top:8px;color:var(--ink)}
.service p{font-size:7.2px;line-height:14px;color:var(--body);margin-top:10px}

/* news */
.section-title{left:124px;top:662px;font-size:12px;font-weight:400}
.news-nav{top:664px;width:14px;height:14px;border-radius:50%;border:1px solid #ccc}
.news-rule{left:124px;top:688px;width:628px;height:1px;background:var(--line)}
.news-photo{top:702px;width:150px;height:116px;border:1px solid #e2e2e2;padding:3px;background:var(--white)}
.news-photo div{width:100%;height:100%}
.news-item{left:288px;top:700px;width:143px}
.news-item h4{font-weight:400;font-size:10.5px;padding-bottom:10px;border-bottom:1px solid var(--line)}
.news-date{font-size:7px;margin-top:10px;display:flex;align-items:center;gap:6px}
.news-date i{width:7px;height:7px;border:1px solid #999}
.news-item p{font-size:7px;line-height:13.6px;color:#333;margin-top:8px}

/* vision */
.vision{left:124px;top:843px;width:628px;height:282px;background:var(--panel);border:1px solid #ececec;overflow:hidden}
.vision h2{position:absolute;left:20px;font-size:15px;font-weight:400;color:#333}
.vision p{position:absolute;left:18px;width:288px;font-size:7.2px;line-height:13.8px;color:var(--muted);text-align:justify}
.vision-art{position:absolute;left:330px;top:70px;width:298px;height:212px;
  background:
    linear-gradient(180deg,rgba(0,0,0,0) 0%,rgba(0,0,0,0) 100%),
    radial-gradient(ellipse 110px 80px at 150px 80px,#6a6a6a 0%,#9a9a9a 60%,rgba(240,240,240,0) 100%),
    linear-gradient(180deg,#f4f4f4 0%,#e4e4e4 55%,#d9c2ae 80%,#aebad0 100%)}

/* footer */
.site-footer{left:0;top:1146px;width:876px;height:54px;background:var(--footer)}
.social{top:1161px;width:22px;height:22px;border-radius:50%}
.copyright{left:351px;top:1168px;font-size:7.5px;color:#ddd}
.badge{top:1161px;height:20px;border-radius:2px}
</style>
</head>
<body>
<div class="page">

  <svg width="0" height="0" style="position:absolute">
    <defs>
      <g id="gear">
        <rect x="-2.2" y="-10" width="4.4" height="5" fill="#fff"/>
        <rect x="-2.2" y="-10" width="4.4" height="5" fill="#fff" transform="rotate(45)"/>
        <rect x="-2.2" y="-10" width="4.4" height="5" fill="#fff" transform="rotate(90)"/>
        <rect x="-2.2" y="-10" width="4.4" height="5" fill="#fff" transform="rotate(135)"/>
        <rect x="-2.2" y="-10" width="4.4" height="5" fill="#fff" transform="rotate(180)"/>
        <rect x="-2.2" y="-10" width="4.4" height="5" fill="#fff" transform="rotate(225)"/>
        <rect x="-2.2" y="-10" width="4.4" height="5" fill="#fff" transform="rotate(270)"/>
        <rect x="-2.2" y="-10" width="4.4" height="5" fill="#fff" transform="rotate(315)"/>
        <circle r="7" fill="#fff"/>
        <circle r="3" fill="#e3232b"/>
      </g>
    </defs>
  </svg>

  <header class="site-header">
    <div class="abs brand"><span class="brand-mark"></span><span class="brand-name">QUELBRANT</span></div>
    <div class="abs partner"><span class="partner-dot"></span>PAGEKILN</div>
    <div class="abs search-field">Search</div>
    <div class="abs search-select">Article</div>
    <div class="abs search-btn">
      <svg width="31" height="24" viewBox="0 0 31 24"><circle cx="14.5" cy="11" r="4.5" fill="none" stroke="#fff" stroke-width="2"/><line x1="17.8" y1="14.3" x2="21" y2="17.5" stroke="#fff" stroke-width="2.4" stroke-linecap="round"/></svg>
    </div>
    <nav class="abs main-nav">
      <span style="left:0">Home</span>
      <span style="left:60px">About Us</span>
      <span style="left:132px">Business units</span>
      <span style="left:237px">Services</span>
      <span style="left:300px">Locations</span>
      <span style="left:376px">Contact</span>
    </nav>
  </header>

  <section class="abs hero" role="img" aria-label="Businessman in a grey suit holding a tablet in front of server racks and a monitor showing a world map"></section>
  <div class="abs hero-title">GOVERNMENT AND COMMERCIAL SECTORS</div>
  <div class="abs hero-sub">quelbrant specializes in delivering</div>
  <div class="abs hero-arrow" style="left:36px;top:256px"><svg width="26" height="26"><path d="M15 8l-5 5 5 5" fill="none" stroke="#666" stroke-width="2"/></svg></div>
  <div class="abs hero-arrow" style="left:805px;top:256px"><svg width="26" height="26"><path d="M11 8l5 5-5 5" fill="none" stroke="#666" stroke-width="2"/></svg></div>

  <section>
    <div class="abs service" style="left:124px">
      <svg width="100" height="100" viewBox="0 0 100 100">
        <circle cx="50" cy="46" r="46" fill="#fff" stroke="#ddd"/>
        <circle cx="50" cy="46" r="42" fill="var(--red)"/>
        <path d="M42 84h16l-8 8z" fill="var(--red)"/>
        <path d="M50 24c-12 0-19 9-19 18 0 10 10 17 15 24h8c5-7 15-14 15-24 0-9-7-18-19-18z" fill="none" stroke="#fff" stroke-width="3"/>
        <rect x="45" y="68" width="10" height="7" fill="#fff"/>
      </svg>
      <h3>Consulting Services</h3>
      <p>Dolore cuml dia sed in lacus ut eniascet inger al es sitet<br>amet eismod ictor ut ligulate ameti dapib ticdu nt<br>mtsent lusto dolorlt comme.</p>
    </div>
    <div class="abs service" style="left:339px">
      <svg width="100" height="100" viewBox="0 0 100 100">
        <circle cx="50" cy="46" r="46" fill="#fff" stroke="#ddd"/>
        <circle cx="50" cy="46" r="42" fill="var(--red)"/>
        <path d="M42 84h16l-8 8z" fill="var(--red)"/>
        <use href="#gear" transform="translate(43 40) scale(1.3)"/>
        <use href="#gear" transform="translate(63 35) scale(0.75)"/>
        <use href="#gear" transform="translate(48 61) scale(0.75)"/>
      </svg>
      <h3>Engineering Services</h3>
      <p>Dolore cuml dia sed in lacus ut eniascet inger al es sitet<br>amet eismod ictor ut ligulate ameti dapib ticdu nt<br>mtsent lusto dolorlt comme.</p>
    </div>
    <div class="abs service" style="left:559px">
      <svg width="100" height="100" viewBox="0 0 100 100">
        <circle cx="50" cy="46" r="46" fill="#fff" stroke="#ddd"/>
        <circle cx="50" cy="46" r="42" fill="var(--red)"/>
        <path d="M42 84h16l-8 8z" fill="var(--red)"/>
        <path d="M50 26l-19 9h38z" fill="#fff"/>
        <rect x="31" y="37" width="38" height="3" fill="#fff"/>
        <rect x="34" y="42" width="4" height="15" fill="#fff"/><rect x="42" y="42" width="4" height="15" fill="#fff"/>
        <rect x="54" y="42" width="4" height="15" fill="#fff"/><rect x="62" y="42" width="4" height="15" fill="#fff"/>
        <rect x="30" y="58" width="40" height="4" fill="#fff"/>
      </svg>
      <h3>Construction Services</h3>
      <p>Dolore cuml dia sed in lacus ut eniascet inger al es sitet<br>amet eismod ictor ut ligulate ameti dapib ticdu nt<br>mtsent lusto dolorlt comme.</p>
    </div>
  </section>

  <section>
    <h2 class="abs section-title">News &amp; Events</h2>
    <div class="abs news-nav" style="left:718px"></div>
    <div class="abs news-nav" style="left:737px"></div>
    <div class="abs news-rule"></div>
    <div class="abs news-photo" style="left:124px"><div role="img" aria-label="Team meeting around a table with a presenter at a flip chart" style="background:linear-gradient(180deg,#e9ecef 0%,#cfd3d8 45%,#6d6a68 75%,#2e2e30 100%)"></div></div>
    <article class="abs news-item">
      <h4>Nam lacinia massa nunc vel.</h4>
      <div class="news-date"><i></i>February 20, 2014</div>
      <p>Lorem ipsum dolor sit amet, consectetur adipiscing elit. Pellentesque rutrum euis-mod turpis, id auctor sapien sagittis eget. Praesent semper enim &nbsp;id auctor sapien sagittis vitae...</p>
    </article>
    <div class="abs news-photo" style="left:443px"><div role="img" aria-label="Three smiling colleagues" style="background:linear-gradient(180deg,#f2f2f2 0%,#e6cdbb 50%,#b98c70 80%,#5a4a40 100%)"></div></div>
    <div class="abs news-photo" style="left:602px"><div role="img" aria-label="Hands reviewing documents beside a keyboard" style="background:linear-gradient(160deg,#2f3338 0%,#dfe3ea 40%,#f3f4f6 60%,#6a6f78 85%,#25282c 100%)"></div></div>
  </section>

  <section class="abs vision">
    <h2 style="top:30px">Quelbrant Our Vision</h2>
    <p style="top:57px">quelbrant specializes in delivering quality professional services and technical projects that support larger business goals. systems are tools that support a greater business function and need. We Understand that Most Technical Projects are conceptualized to support A larger Vision with Actual business goals in Mind and ensure that all of our Professional and Certified Expertise is Included in our Professional Services to meet those goals.</p>
    <h2 style="top:154px">Our Goals</h2>
    <p style="top:183px">we have the expertise to deliver the exclusive system. And technical quality. To support and accommodate larger business goals. Our management system is a tool that supports the model and business needs. We understand that the most technical concepts that support the vision of a true business goals. We will take steps to ensure that the knowledge and expertise of our. Be in the professional services we deliver to our customers to achieve such goals.</p>
    <div class="vision-art" role="img" aria-label="Hands holding a tablet showing a rising bar chart"></div>
  </section>

  <footer>
    <div class="abs site-footer"></div>
    <span class="abs social" style="left:125px;background:#3aa7e0"></span>
    <span class="abs social" style="left:153px;background:#3b5ea8"></span>
    <span class="abs social" style="left:182px;background:#666"></span>
    <span class="abs social" style="left:211px;background:#e0488e"></span>
    <div class="abs copyright">Copyright@2014 quelbrant.. All Right Reserved</div>
    <span class="abs badge" style="left:639px;width:60px;background:#2f6fb5;border:1px solid #9cc"></span>
    <span class="abs badge" style="left:703px;width:49px;top:1164px;height:14px;background:#eee"></span>
  </footer>

</div>
</body>
</html>
```